Group training gym/bootcamp needs a web design

We need a website for our gym that is based in Sydney. We have indoor functional training classes and outdoor bootcamp classes. We would like the web site to have a video (to be created) and photo gallery. I would like the site made on word press and i would like to be able to make minor changes such as changing images and text without having to use a designer.

The website should have the following pages: home page; the gym; the bootcamp; photo gallery; about us; contact.

I have uploaded our logo and i would like to keep to these colour (blue,yellow,silver) and black is also allowed

Target Market(s)

18-50 male and female

Industry/Entity Type

Gym

Coding

Coded - Design and coding required

Number of Pages Required

5+ page

Font styles to use
Sans Serif

Colors
0692cd
fbed22
1b1b1b
e8e8e8

Requirements
Must have
• The website should have the following pages: home page; the gym; the bootcamp; photo gallery; about us; contact.
• I have uploaded our logo and i would like to keep to these colour (blue,yellow,silver) and black is also allowed
• Video upload and photo upload

```html
<!DOCTYPE html>
<html lang="en">
<head>
<meta charset="utf-8">
<title>Ironbay Training Yard – About Us</title>
<link rel="stylesheet" href="https://fonts.googleapis.com/css2?family=Oswald:wght@500;600&family=Open+Sans:wght@400&family=Roboto:wght@300;400&family=Lato:wght@300;700&display=swap">
<style>
  :root {
    --blue: #2a88c8;
    --blue-bright: #0692cd;
    --yellow: #f2c318;
    --ink: #1b1b1b;
    --silver: #e8e8e8;
    --text-grey: #777777;
    --dark-navy: #0e1c28;
    --orange: #f0531c;
    --white: #ffffff;
  }
  * { box-sizing: border-box; margin: 0; padding: 0; }
  html, body { width: 974px; height: 1200px; overflow: hidden; background: var(--white); }
  body { position: relative; font-family: "Open Sans", sans-serif; }

  .site-header {
    position: absolute; left: 0; top: 0; width: 974px; height: 174px;
    background: radial-gradient(ellipse at 50% 40%, #24384a 0%, #132433 55%, var(--dark-navy) 100%);
  }
  .brand {
    position: absolute; left: 0; right: 0; display: flex; align-items: center; justify-content: center; gap: 8px;
    font-family: "Oswald", sans-serif; font-weight: 600; color: var(--yellow); letter-spacing: 1px;
  }
  .brand-dot { border-radius: 50%; background: var(--blue-bright); }
  .site-header .brand { top: 44px; font-size: 20px; }
  .site-header .brand-dot { width: 18px; height: 18px; }

  .main-nav {
    position: absolute; top: 104px; left: 0; right: 0;
    display: flex; justify-content: center; gap: 23px;
    font-family: "Oswald", sans-serif; font-weight: 500; font-size: 12.5px; color: var(--white);
  }
  .main-nav .current { color: var(--yellow); }

  .about-title {
    position: absolute; left: 151px; top: 198px;
    font-family: "Oswald", sans-serif; font-weight: 600; font-size: 52px; line-height: 1; color: var(--blue);
  }
  .about-copy { position: absolute; left: 152px; top: 278px; width: 432px; }
  .about-copy p { font-size: 10px; line-height: 14.6px; color: var(--text-grey); margin-bottom: 14.6px; }

  .feature { position: absolute; left: 152px; width: 432px; }
  .feature h3 {
    display: flex; align-items: center; gap: 7px;
    font-family: "Roboto", sans-serif; font-weight: 400; font-size: 13.2px; color: var(--ink);
  }
  .feature p {
    margin: 8px 0 0 22px; font-size: 9.2px; line-height: 16px; color: var(--text-grey);
  }

  .photo-frame { position: absolute; left: 602px; top: 222px; width: 220px; height: 276px; }
  .photo-frame .accent {
    position: absolute; left: 10px; top: 0; width: 210px; height: 262px;
    background: var(--orange); transform: rotate(1deg);
  }
  .photo-frame .photo {
    position: absolute; left: 0; top: 16px; width: 210px; height: 260px;
    background: linear-gradient(135deg, #c9d4df 0%, #e3d2c2 45%, #9fb0c2 100%);
  }
  .photo-frame .photo::after {
    content: ""; position: absolute; inset: 6px 8px 12px 8px; border: 1px dashed rgba(255,255,255,.8);
  }

  .promo {
    position: absolute; left: 0; top: 681px; width: 974px; height: 333px;
    background: linear-gradient(90deg, #3a4046 0%, #22262a 35%, #141414 60%, #121212 100%);
  }
  .promo-copy { position: absolute; left: 344px; top: 74px; color: var(--white); font-family: "Lato", sans-serif; }
  .promo-copy h2 { font-weight: 700; font-size: 29px; letter-spacing: .5px; }
  .promo-copy .offer { margin-top: 12px; font-weight: 300; font-size: 29px; line-height: 34px; }
  .promo-copy .offer em { font-style: normal; color: var(--yellow); }
  .join-button {
    display: inline-block; margin-top: 21px; width: 144px; height: 36px; line-height: 36px; text-align: center;
    border-radius: 10px; background: var(--blue);
    font-family: "Oswald", sans-serif; font-weight: 500; font-size: 15px; color: var(--white);
  }

  .site-footer .brand { top: 1060px; font-size: 18px; }
  .site-footer .brand-dot { width: 16px; height: 16px; }
  .social { position: absolute; top: 1125px; left: 0; right: 0; display: flex; justify-content: center; gap: 9px; }
  .social span { width: 18px; height: 18px; border: 1.4px solid var(--ink); border-radius: 50%; }
  .copyright {
    position: absolute; top: 1152px; left: 0; right: 0; text-align: center;
    font-family: "Roboto", sans-serif; font-weight: 300; font-size: 11.5px; color: var(--text-grey);
  }
  .footer-bar { position: absolute; left: 0; top: 1177px; width: 974px; height: 23px; }
</style>
</head>
<body>
  <header class="site-header" role="img" aria-label="Dark-toned photo of a lifter holding two dumbbells">
    <div class="brand"><span class="brand-dot"></span>IRONBAY TRAINING YARD</div>
    <nav class="main-nav">
      <span>HOME</span><span>THE GYM</span><span>THE BOOTCAMP</span><span>PHOTO GALLERY</span><span class="current">ABOUT US</span><span>CONTACT</span>
    </nav>
  </header>

  <h1 class="about-title">ABOUT US</h1>
  <div class="about-copy">
    <p>Quisque et lectus pulvinar, porttitor mi non, elementum dui. Morbi mi nisl, tincidunt sed venenatis eget, finibus eu mauris. Nullam nisi lacus, feugiat eget varegeellentesque dictum odio. Sed sollicitudin viverra est, at aliquam metus ultrices id. Duis eu purus vel nisl commodo facilisis vitae ut lectus. Sed elementum dapibus tellus, a dictum metus interdum ac. Nullam condimentum, dui volutpat fringilla molestie, libero tortor ultrices lorem, at tempus diam purus non velit. Aliquam vel nulla eleifend, consequat elit id, tristique massa. Fusce dolor velit, blandit ac erat ac, vestibulum ornare diam.</p>
    <p>Sed sollicitudin viverra est, at aliquam metu eratys ultrices tristique massaid.diam purus non velit. Aliquam vel nulla eleifend, consequat elit id, tristique massa. Fusce dolor velit, blandit ac erat ac, vestibulum ornare diam. Sed sollicitudin viverra.</p>
  </div>

  <section class="feature" style="top:457px">
    <h3><svg width="15" height="12" viewBox="0 0 15 12"><path d="M1 6.5 L5.5 10.5 L14 1.5" fill="none" stroke="#2a88c8" stroke-width="3"/></svg>We have Gym Trainer</h3>
    <p>Sed elementum dapibus tellus, a dictum metus interdum ac. Nullam condimentum, dui volutpat fringilla molestie, libero tortor ultrices lorem, at tempus diam purus non velit. Aliquam vel nulla eleifend, consequat elit id, tristique massdolor velit, blandi.</p>
  </section>
  <section class="feature" style="top:548px">
    <h3><svg width="15" height="12" viewBox="0 0 15 12"><path d="M1 6.5 L5.5 10.5 L14 1.5" fill="none" stroke="#2a88c8" stroke-width="3"/></svg>Modern Gym &amp; Fitness Facilities</h3>
    <p>Sed elementum dapibus tellus, a dictum metus interdum ac. Nullam condimentum, dui volutpat fringilla molestie, libero tortor ultrices lorem, at tempus diam purus non velit. Aliquam vel nulla eleifend, consequat elit id, tristique massdolor velit, blandi.</p>
  </section>

  <figure class="photo-frame">
    <div class="accent"></div>
    <div class="photo" role="img" aria-label="Photo of a smiling woman lifting a dumbbell in a gym"></div>
  </figure>

  <section class="promo" role="img" aria-label="Dark photo of a runner's leg on a treadmill">
    <div class="promo-copy">
      <h2>FITNESS CLASSES THIS SUMMER</h2>
      <p class="offer">PAY NOW AND<br><em>GET 35%</em> DISCOUNT</p>
      <span class="join-button">BECOME A MEMBER</span>
    </div>
  </section>

  <footer class="site-footer">
    <div class="brand"><span class="brand-dot"></span>IRONBAY TRAINING YARD</div>
    <div class="social"><span></span><span></span><span></span><span></span></div>
    <p class="copyright">Copyright © Ironbay Training Yard 2017. All Rights Reserved | Privacy Policy | Terms of Use</p>
    <svg class="footer-bar" viewBox="0 0 974 23" preserveAspectRatio="none">
      <path d="M0 18 H456 L486 0 L516 18 H974 V23 H0 Z" fill="#2a88c8"/>
    </svg>
  </footer>
</body>
</html>
```